Moravel Aesthetic Doctor

I require an elegant, luxurious looking business card for my aesthetic business. I am a doctor and that will set me aside from competitors. I am planning to provide home and spa based treatments to clients with high expectations. I have attached my logo.

```html
<!DOCTYPE html>
<html lang="en">
<head>
<meta charset="utf-8">
<title>Moravel Aesthetic Doctor – Business Card</title>
<link rel="stylesheet" href="https://fonts.googleapis.com/css2?family=Cormorant+Garamond:wght@400;600&family=Quicksand:wght@400;500&display=swap">
<style>
  :root {
    --bg: #e4e6e9;
    --card: #ffffff;
    --sky: #00a9ea;
    --sky-light: #7cc6ee;
    --silver: #9a9ea3;
    --ink: #6f7276;
    --white: #ffffff;
  }
  * { margin: 0; padding: 0; box-sizing: border-box; }
  html, body { width: 1200px; height: 965px; overflow: hidden; background: var(--bg); }
  .card {
    position: absolute; left: 220px; width: 760px; height: 430px;
    background: var(--card); overflow: hidden;
    box-shadow: 0 6px 18px rgba(0,0,0,.18);
  }
  .card-front { top: 40px; }
  .card-back { top: 495px; }

  .brand { position: absolute; display: flex; align-items: center; gap: 22px; }
  .brand-mark { width: 120px; height: 120px; border-radius: 50%; border: 4px solid var(--silver); flex: none; }
  .brand-name {
    font-family: "Cormorant Garamond", serif; font-weight: 400;
    color: var(--ink); line-height: .95;
  }
  .brand-name .big { display: block; font-size: 74px; letter-spacing: 3px; text-transform: uppercase; }
  .brand-name .small { display: block; font-size: 30px; letter-spacing: 2px; text-transform: uppercase; }
  .card-front .brand { left: 150px; top: 120px; }
  .card-back .brand { left: 55px; top: 45px; }
  .card-back .brand-mark { width: 100px; height: 100px; }
  .card-back .brand-name .big { font-size: 60px; }
  .card-back .brand-name .small { font-size: 25px; }

  .rule { position: absolute; height: 1.5px; background: var(--silver); }
  .rule-top { left: 540px; top: 250px; width: 160px; }
  .tagline-row { position: absolute; left: 60px; right: 60px; top: 340px; display: flex; align-items: center; gap: 18px; }
  .tagline-row .rule { position: static; flex: 1; }
  .tagline {
    font-family: "Cormorant Garamond", serif; font-weight: 600;
    font-size: 20px; letter-spacing: 1.5px; color: var(--sky); text-transform: uppercase;
  }

  .social { position: absolute; left: 590px; top: 55px; display: flex; gap: 12px; }
  .social span { width: 18px; height: 18px; border-radius: 50%; background: var(--sky); }

  .wave { position: absolute; inset: 0; }

  .person { position: absolute; left: 40px; top: 285px; color: var(--white); }
  .person-name { font-family: "Cormorant Garamond", serif; font-weight: 600; font-size: 34px; }
  .person-name .creds { font-family: "Quicksand", sans-serif; font-weight: 400; font-size: 20px; border-left: 2px solid var(--white); padding-left: 10px; margin-left: 8px; }
  .person-title { font-family: "Quicksand", sans-serif; font-size: 17px; margin-top: 2px; }

  .contacts { position: absolute; left: 60px; top: 360px; list-style: none; color: var(--white); font-family: "Quicksand", sans-serif; font-size: 17px; }
  .contacts li { display: flex; align-items: center; gap: 10px; height: 21px; }
  .contacts li b { font-weight: 500; }
  .contacts svg { width: 15px; height: 15px; }

  .divider { position: absolute; left: 400px; top: 300px; width: 2px; height: 90px; background: var(--white); opacity: .85; }
  .services { position: absolute; left: 425px; top: 300px; list-style: none; color: var(--white); font-family: "Quicksand", sans-serif; font-size: 16px; line-height: 1.5; }
</style>
</head>
<body>
  <section class="card card-front">
    <div class="brand">
      <div class="brand-mark" role="img" aria-label="Brand emblem"></div>
      <div class="brand-name"><span class="big">Moravel</span><span class="small">Aesthetic Doctor</span></div>
    </div>
    <div class="rule rule-top"></div>
    <div class="tagline-row">
      <div class="rule"></div>
      <p class="tagline">Home and Spa Based Treatments</p>
      <div class="rule"></div>
    </div>
  </section>

  <section class="card card-back">
    <svg class="wave" viewBox="0 0 760 430" preserveAspectRatio="none" aria-hidden="true">
      <path d="M0,262 C250,248 460,120 760,20 L760,430 L0,430 Z" fill="var(--silver)"/>
      <path d="M0,278 C260,262 470,138 760,48 L760,430 L0,430 Z" fill="var(--sky)"/>
    </svg>
    <div class="brand">
      <div class="brand-mark" role="img" aria-label="Brand emblem"></div>
      <div class="brand-name"><span class="big">Moravel</span><span class="small">Aesthetic Doctor</span></div>
    </div>
    <div class="social" aria-label="Social links"><span></span><span></span></div>

    <div class="person">
      <p class="person-name">Dr Lena Marsh<span class="creds">MRCPCH MD</span></p>
      <p class="person-title">Australasian Diploma of Aesthetic Medicine</p>
    </div>

    <ul class="contacts">
      <li><svg viewBox="0 0 16 16"><path d="M4 1.5l2.5 3-1.5 2c1 2 2.5 3.5 4.5 4.5l2-1.5 3 2.5-1.5 2.5C7.5 15 1 8.5 1.5 3z" fill="none" stroke="#fff" stroke-width="1.3"/></svg>0800 555 017</li>
      <li><svg viewBox="0 0 16 16"><rect x="1" y="3" width="14" height="10" fill="none" stroke="#fff" stroke-width="1.3"/><path d="M1 3l7 6 7-6" fill="none" stroke="#fff" stroke-width="1.3"/></svg>lena@moravel.co.nz</li>
      <li><svg viewBox="0 0 16 16"><circle cx="8" cy="8" r="7" fill="none" stroke="#fff" stroke-width="1.3"/><ellipse cx="8" cy="8" rx="3" ry="7" fill="none" stroke="#fff" stroke-width="1.1"/><path d="M1 8h14" stroke="#fff" stroke-width="1.1"/></svg>www.<b>moravel</b>.co.nz</li>
    </ul>

    <div class="divider"></div>
    <ul class="services">
      <li>Dermal injectables - Plasma facials - Microneedling</li>
      <li>Skin boosters - Excessive sweating</li>
      <li>Home and Spa Based Treatments</li>
    </ul>
  </section>
</body>
</html>
```